Business Card Design for Online Gift Business

Business card design for a new online Canadian company called "Harlow & Brine Gift Boxes" selling modern and luxurious gift boxes for every occasion. Items are sourced locally from talented socially-responsible Canadian artisans. Each gift is elegantly presented in a keepsake wood box to ensure a lasting impression.

Industry/Entity Type

E-Commerce

Contact Information for Business Card

Marla Whitcombe, Proprietor
Brookmere, AB
403-555-2741
www.harlowandbrine.ca
hello@harlowandbrine.ca

Requirements
Must have
• Boxed with care, given with heart
• Please also include the symbols for Facebook and Instagram
Nice to have
• **I have attached a few samples of background colors and font colors that I like. I hope this helps in a few directions to try.

```html
<!DOCTYPE html>
<html lang="en">
<head>
<meta charset="utf-8">
<title>Harlow &amp; Brine Gift Boxes – Business Card</title>
<link rel="stylesheet" href="https://fonts.googleapis.com/css2?family=Bebas+Neue&display=swap">
<style>
  :root {
    --backdrop: #aab6b6;
    --card: #f3f0ef;
    --ink: #231f20;
    --rule: #4a4546;
  }
  * { margin: 0; padding: 0; box-sizing: border-box; }
  html, body {
    width: 1200px; height: 824px; overflow: hidden;
    background: var(--backdrop);
  }
  .sheet {
    width: 1200px; height: 824px;
    display: flex; align-items: center; justify-content: center; gap: 40px;
  }
  .card {
    width: 540px; height: 309px;
    background: var(--card);
    color: var(--ink);
    font-family: "Bebas Neue", "Oswald", sans-serif;
    display: flex; flex-direction: column; align-items: center; justify-content: center;
    box-shadow: 0 2px 6px rgba(0, 0, 0, 0.12);
  }

  /* Contact side */
  .contact-side .mark-dot {
    width: 12px; height: 12px; border-radius: 50%;
    background: var(--ink); margin-bottom: 6px;
  }
  .rule-pair { width: 260px; display: flex; flex-direction: column; gap: 3px; }
  .rule-pair span { display: block; height: 0; border-top: 1px dotted var(--rule); }
  .rule-pair span + span { border-top-style: solid; }
  .holder-name { font-size: 34px; font-weight: 400; letter-spacing: 0.5px; line-height: 1; margin: 6px 0 2px; }
  .holder-role {
    display: flex; align-items: center; gap: 6px;
    font-size: 17px; letter-spacing: 1px; margin-bottom: 6px;
  }
  .holder-role::before, .holder-role::after {
    content: ""; width: 18px; border-top: 1px solid var(--rule);
  }
  .contact-list { list-style: none; text-align: center; margin-top: 10px; font-size: 15px; line-height: 1.2; letter-spacing: 0.5px; }
  .social-row { display: flex; gap: 6px; margin-top: 6px; }
  .social-dot { width: 14px; height: 14px; border-radius: 50%; border: 1.5px solid var(--ink); }

  /* Brand side */
  .brand-name { font-size: 60px; font-weight: 400; letter-spacing: 4px; line-height: 1; }
  .tagline { font-size: 21px; letter-spacing: 0.5px; margin-top: 18px; }
</style>
</head>
<body>
<main class="sheet">
  <section class="card contact-side">
    <div class="mark-dot"></div>
    <div class="rule-pair"><span></span><span></span></div>
    <h1 class="holder-name">Marla Whitcombe</h1>
    <p class="holder-role">Proprietor</p>
    <div class="rule-pair"><span></span><span></span></div>
    <ul class="contact-list">
      <li>Brookmere, AB</li>
      <li>www.harlowandbrine.ca</li>
      <li>403-555-2741</li>
    </ul>
    <div class="social-row">
      <span class="social-dot"></span>
      <span class="social-dot"></span>
    </div>
  </section>

  <section class="card brand-side">
    <h2 class="brand-name">Harlow &amp; Brine</h2>
    <p class="tagline">Boxed with care, given with heart</p>
  </section>
</main>
</body>
</html>
```